Veltrane Group Business Card Design

The CEO is looking for a new trendy look for his business card.
You can stay with current branding or come up with something new/creative. It can be 3D, including Medical Office buildings. You can use our logo in a variety of colors. Please include name, title, company name, company website, email address, cell number

Target Market(s)

Real Estate Development and Construction

Industry/Entity Type

Health care real estate

Contact Information for Business Card

Rohesh Kamdar, CEO M-604.781.2249 E-roheshkamdar@veltrane.com Address:4180 Lindqvist Ave, Tampa, FL 33482 www.veltrane.com

Font styles to use
Other font styles liked:
• Be creative

Requirements
Must have
• Creative, trendy look
Nice to have
• Please go to our website to get a feel- www. veltrane.com
Should not have
• small fonts

```html
<!DOCTYPE html>
<html lang="en">
<head>
<meta charset="utf-8">
<title>Veltrane Group Business Card</title>
<link rel="stylesheet" href="https://fonts.googleapis.com/css2?family=Montserrat:wght@400;700;800&display=swap">
<style>
  :root {
    --bg: #e9e9ec;
    --navy: #1e2f4f;
    --navy-light: #2b4670;
    --red: #b01e25;
    --ink: #2a2a2a;
    --paper: #ffffff;
  }
  * { box-sizing: border-box; margin: 0; padding: 0; }
  html, body { width: 1200px; height: 913px; overflow: hidden; }
  body {
    background: var(--bg);
    font-family: "Montserrat", sans-serif;
    position: relative;
  }
  .card {
    position: absolute;
    width: 560px;
    height: 320px;
    border-radius: 22px;
    box-shadow: 0 4px 0 var(--red), 0 14px 30px rgba(0,0,0,0.18);
    overflow: hidden;
  }
  .card-back {
    left: 60px;
    top: 90px;
    background: var(--navy);
    display: flex;
    align-items: center;
    justify-content: center;
  }
  .back-wordmark {
    color: var(--navy-light);
    font-weight: 800;
    font-size: 62px;
    letter-spacing: -1px;
  }
  .card-front {
    left: 580px;
    top: 480px;
    background: var(--paper);
  }
  .front-wordmark {
    position: absolute;
    right: 40px;
    top: 42px;
    color: var(--red);
    font-weight: 800;
    font-size: 42px;
    letter-spacing: -1px;
  }
  .divider {
    position: absolute;
    left: 40px;
    right: 40px;
    top: 196px;
    height: 2px;
    background: var(--red);
  }
  .identity {
    position: absolute;
    left: 40px;
    top: 130px;
  }
  .person-name {
    color: var(--red);
    font-weight: 700;
    font-size: 26px;
    letter-spacing: 0.5px;
    text-transform: uppercase;
    line-height: 1;
  }
  .person-title {
    color: var(--ink);
    font-size: 20px;
    margin-top: 6px;
    line-height: 1;
  }
  .contacts {
    position: absolute;
    left: 40px;
    top: 214px;
    list-style: none;
  }
  .contacts li {
    display: flex;
    align-items: center;
    gap: 10px;
    font-size: 17px;
    color: var(--ink);
    height: 30px;
  }
  .contacts svg { width: 14px; height: 14px; flex: none; }
  .address {
    position: absolute;
    right: 40px;
    top: 218px;
    text-align: right;
    font-size: 16px;
    line-height: 1.5;
    color: var(--ink);
    font-style: normal;
  }
</style>
</head>
<body>
  <section class="card card-back" aria-label="Card back">
    <span class="back-wordmark">Veltrane Group</span>
  </section>

  <section class="card card-front" aria-label="Card front">
    <span class="front-wordmark">Veltrane Group</span>
    <div class="identity">
      <p class="person-name">Rohesh Kamdar</p>
      <p class="person-title">CEO</p>
    </div>
    <div class="divider"></div>
    <ul class="contacts">
      <li>
        <svg viewBox="0 0 14 14" aria-hidden="true"><rect x="3" y="0.5" width="8" height="13" rx="1.5" fill="none" stroke="#b01e25" stroke-width="1.6"/><circle cx="7" cy="11" r="0.9" fill="#b01e25"/></svg>
        604.781.2249
      </li>
      <li>
        <svg viewBox="0 0 14 14" aria-hidden="true"><rect x="0.5" y="2.5" width="13" height="9" fill="#b01e25"/><path d="M0.5 2.5 L7 8 L13.5 2.5" fill="none" stroke="#fff" stroke-width="1.2"/></svg>
        roheshkamdar@veltrane.com
      </li>
      <li>
        <svg viewBox="0 0 14 14" aria-hidden="true"><circle cx="7" cy="7" r="6.5" fill="#b01e25"/><path d="M0.5 7 H13.5 M7 0.5 C3.5 4 3.5 10 7 13.5 M7 0.5 C10.5 4 10.5 10 7 13.5" fill="none" stroke="#fff" stroke-width="0.9"/></svg>
        www.veltrane.com
      </li>
    </ul>
    <address class="address">4180 Lindqvist Ave,<br>Tampa, FL 33482</address>
  </section>
</body>
</html>
```